Tovin Brightway Website Design

About The Client:
Tovin Brightway is a sugar-free foods chain store providing services to Diabetics. They focus on the China domestic market. They describe themselves as being the 3rd space for Diabetics, the space between hospital and the home that help improve the quality of life for people wit Diabetes (see attached infographics).

They regularly hold education and advice events throughout the China. Tovin Brightway distribute a wide product range of food that is suitable for diabetic people. Tovin Brightway operate as a Franchise, providing business development services and Industry knowledge. They are actively seeking business partnerships at present.

The Brief:
Design a Home page and secondary information page(PSD only no code) that communicates our company services and company philosophy(3rd Space).
The final design should communicate 'Health, Social Responsibility and Professionalism'.
Colour scheme should orientate around Blue and White, see attached logo.

Websites we like:

http://lumo.vextaran.com/home/

https://www.pondrelix.com/

http://gate.zt.com/

Hello all, the client has advised us that he want to display the professional advice service available for diabetic people more so than a food distributor. The client is also hoping to use his website as a marketing platform to attract affiliates and build partnerships as part of Tovin Brightway's business expansion strategy.

So can you make the page more corporate, reliable and professional. Use images of experts/doctors interacting with patients and also training/knowledge transfer images.

Thanks

Hello all, could you include stock images of both Chinese and Caucasians

Yeaahhh, Infographics and photos have been uploaded. Feel free to use them in your designs and also as references.

Target Market(s)

The target market is Chinese B2B in the Diabetics industry and Entrepreneurs looking to cooperate with Tovin Brightway.

Industry/Entity Type

Education

Requirements
Must have
• menu navigation with 7-8 sections,
a full screen background image,
Social Media icons,
Logo in top left,
Site search.
Nice to have
• The website must be clear and easy to use, less complicated.

See attached files of some Tovin Brightway infographics. Feel free to include elements of these into the design.
Should not have
• Should not use stock images of people from any other country, the client wants stock images of Chinese people only. Avoid photos showing obesity.

```html
<!DOCTYPE html>
<html lang="en">
<head>
<meta charset="utf-8">
<title>Tovin Brightway — Home</title>
<link rel="stylesheet" href="https://fonts.googleapis.com/css2?family=Source+Sans+3:wght@400;600&display=swap">
<style>
:root{
  --blue:#2a74b6;
  --blue-dark:#1e5d98;
  --blue-text:#1f6fae;
  --red:#d2232a;
  --grey-band:#eeeeee;
  --grey-text:#555555;
  --line:#d9d9d9;
  --footer:#555658;
  --footer-dark:#3f4042;
  --white:#ffffff;
}
*{margin:0;padding:0;box-sizing:border-box}
html,body{width:1151px;height:1200px;overflow:hidden;background:var(--white)}
body{font-family:"Source Sans 3",sans-serif;color:var(--grey-text);position:relative}
.abs{position:absolute}
.topline{left:0;top:0;width:1151px;height:3px;background:var(--blue)}
.brand{left:187px;top:22px;display:flex;align-items:center;gap:8px;color:var(--blue);font-size:19px;font-weight:600}
.brand-mark{width:40px;height:40px;background:var(--blue)}
.search{left:570px;top:39px;width:218px;height:23px;border:1px solid #cfcfcf;border-radius:3px;background:#f4f4f4;font-size:8px;color:#777;padding:6px 9px;letter-spacing:.3px}
.search svg{position:absolute;right:8px;top:5px}
.lang-label{left:804px;top:43px;font-size:9px;color:#666}
.lang{left:882px;top:39px;width:95px;height:23px;border:1px solid #cfcfcf;border-radius:3px;background:#fafafa;font-size:9.5px;color:#333;padding:5px 0 0 31px}
.lang .flag{position:absolute;left:8px;top:6px;width:15px;height:10px;background:#2c4a8c}
.lang svg{position:absolute;right:8px;top:8px}
.nav{left:0;top:97px;width:1151px;height:38px;background:var(--blue);border-bottom:2px solid var(--blue-dark)}
.nav ul{list-style:none;position:absolute;left:173px;top:0;height:38px;display:flex}
.nav li{height:38px;line-height:38px;color:var(--white);font-size:10px;text-align:center;letter-spacing:-.1px}
.nav li.active{background:var(--blue-dark)}
.hero{left:0;top:135px;width:1151px;height:392px;background:var(--white)}
.hero-photo{left:111px;top:18px;width:560px;height:374px;background:linear-gradient(90deg,#ffffff 0%,#e6e2e6 10%,#7d6f78 35%,#6a3f86 65%,#e9e6ee 88%,#ffffff 100%)}
.hero-arrow{width:60px;height:60px;border-radius:50%;background:#c8c8c8;top:155px}
.hero-arrow svg{position:absolute;left:20px;top:17px}
.hero-text{left:561px;top:154px;font-size:21px;font-weight:600;line-height:33px;color:var(--blue)}
.hero-text .hl{color:var(--red)}
.services{left:0;top:527px;width:1151px;height:228px;background:var(--grey-band)}
.sec-title{font-size:17px;color:var(--red);font-weight:400;text-align:center;letter-spacing:-.2px}
.svc{width:180px;text-align:center;top:60px}
.svc-icon{width:66px;height:66px;border-radius:50%;margin:0 auto;background:#dcdcdc;display:flex;align-items:center;justify-content:center}
.svc-icon span{width:56px;height:56px;border-radius:50%;background:linear-gradient(#8a8a8a,#5c5c5c);display:flex;align-items:center;justify-content:center}
.svc-icon.on span{background:linear-gradient(#58a6e6,#2a74b6)}
.svc h3{font-size:12.5px;font-weight:400;color:var(--blue-text);margin-top:10px}
.svc p{font-size:8.6px;line-height:14.5px;margin-top:8px;color:#555}
.about-title{left:0;top:771px;width:1151px}
.about-text{left:180px;top:801px;width:790px;text-align:center;font-size:9.4px;line-height:16.5px;color:#444}
.divider{left:173px;top:854px;width:805px;height:1px;background:var(--line)}
.block-title{font-size:17px;color:var(--red);top:875px;letter-spacing:-.2px}
.pager{top:882px;display:flex;gap:6px}
.card{width:167px;top:912px}
.card-img{width:167px;height:84px;border:1px solid #d2d2d2;background:var(--white);display:flex;align-items:center;justify-content:center}
.card-img div{width:70px;height:70px;background:linear-gradient(#f0c24a,#c6551e)}
.item-title{font-size:11.5px;color:var(--blue-text);margin-top:18px}
.item-desc{font-size:8.6px;line-height:16px;color:#555;margin-top:4px}
.price{font-size:13px;color:var(--red);position:absolute;top:172px;left:0}
.btn{position:absolute;width:73px;height:21px;border-radius:2px;background:linear-gradient(#67b1ea,#2d7cc2);color:var(--white);font-size:8px;text-align:center;line-height:21px}
.tip{left:750px;width:228px}
.tip-img{width:64px;height:54px;border:1px solid #d2d2d2;background:linear-gradient(135deg,#c9d2d8,#b23a2a)}
.tip-body{position:absolute;left:80px;top:0;width:148px}
.tip-body .item-title{margin-top:4px}
.tip-body .item-desc{line-height:15px}
.tip-sep{left:750px;top:981px;width:228px;height:1px;background:var(--line)}
.footer{left:0;top:1126px;width:1151px;height:74px;background:linear-gradient(var(--footer),var(--footer-dark))}
.foot-links{left:175px;top:20px;font-size:7.6px;color:var(--white);display:flex;gap:0;letter-spacing:-.1px}
.foot-links span{padding:0 8px}
.foot-links span:first-child{padding-left:0}
.copy{left:175px;top:43px;font-size:7.6px;color:var(--white)}
.follow{left:838px;top:31px;font-size:7.6px;color:var(--white)}
.soc{width:26px;height:26px;border-radius:50%;top:23px}
</style>
</head>
<body>
<div class="abs topline"></div>

<header>
  <div class="abs brand"><span class="brand-mark"></span>Tovin Brightway</div>
  <div class="abs search">SEARCH :
    <svg width="11" height="11" viewBox="0 0 11 11"><circle cx="4.5" cy="4.5" r="3.5" fill="none" stroke="#bbb" stroke-width="1.2"/><line x1="7" y1="7" x2="10" y2="10" stroke="#bbb" stroke-width="1.2"/></svg>
  </div>
  <div class="abs lang-label">Select Language :</div>
  <div class="abs lang"><span class="flag"></span>English
    <svg width="8" height="5" viewBox="0 0 8 5"><path d="M1 1l3 3 3-3" fill="none" stroke="#333" stroke-width="1.4"/></svg>
  </div>
</header>

<nav class="abs nav">
  <ul>
    <li class="active" style="width:90px">HOME</li>
    <li style="width:80px">ABOUT US</li>
    <li style="width:100px">SERVICES</li>
    <li style="width:84px">PRODUCTS</li>
    <li style="width:65px">FAQ</li>
    <li style="width:80px">TIPS</li>
    <li style="width:100px">TESTIMONIALS</li>
    <li style="width:100px">FEATURES</li>
    <li style="width:98px">CONTACT US</li>
  </ul>
</nav>

<section class="abs hero">
  <div class="abs hero-photo" role="img" aria-label="Photo of a smiling senior Chinese couple sitting together"></div>
  <div class="abs hero-arrow" style="left:110px"><svg width="20" height="26" viewBox="0 0 20 26"><path d="M15 2L4 13l11 11" fill="none" stroke="#fff" stroke-width="2" stroke-dasharray="2 2"/></svg></div>
  <div class="abs hero-arrow" style="left:989px"><svg width="20" height="26" viewBox="0 0 20 26"><path d="M5 2l11 11L5 24" fill="none" stroke="#fff" stroke-width="2" stroke-dasharray="2 2"/></svg></div>
  <div class="abs hero-text">
    <div class="hl">GROUP OF SUGAR FREE FOOD CHAIN STORES</div>
    <div>IN CHINA PROVIDING SERVICES</div>
    <div>TO DIABETES.</div>
  </div>
</section>

<section class="abs services">
  <h2 class="abs sec-title" style="left:0;top:20px;width:1151px">OUR SERVICES</h2>
  <div class="abs svc" style="left:173px">
    <div class="svc-icon on"><span><svg width="30" height="26" viewBox="0 0 30 26"><path d="M5 12a10 10 0 0 1 18-5" fill="none" stroke="#fff" stroke-width="3.5"/><path d="M25 1v8h-8z" fill="#fff"/><path d="M25 14a10 10 0 0 1-18 5" fill="none" stroke="#fff" stroke-width="3.5"/><path d="M5 25v-8h8z" fill="#fff"/></svg></span></div>
    <h3>SOCIAL COMMUNICATION</h3>
    <p>Lorem Ipsum is simply dummy text of the printing and typesetting industry. Lorem Ipsum has been the industry's standard...</p>
  </div>
  <div class="abs svc" style="left:385px">
    <div class="svc-icon"><span><svg width="30" height="24" viewBox="0 0 30 24"><path d="M3 12h24a12 10 0 0 1-24 0z" fill="none" stroke="#fff" stroke-width="1.8"/><path d="M8 10c0-4 14-4 14 0" fill="none" stroke="#fff" stroke-width="1.5"/><path d="M13 1v5M16 1v5" stroke="#fff" stroke-width="1"/></svg></span></div>
    <h3>FOOD ADVICE</h3>
    <p>Lorem Ipsum is simply dummy text of the printing and typesetting industry. Lorem Ipsum has been the industry's standard...</p>
  </div>
  <div class="abs svc" style="left:587px">
    <div class="svc-icon"><span><svg width="26" height="28" viewBox="0 0 26 28"><path d="M9 3h8M11 3v8L4 24h18L15 11V3" fill="none" stroke="#fff" stroke-width="1.8" transform="rotate(25 13 14)"/></svg></span></div>
    <h3>CHECKUP PRODUCTS</h3>
    <p>Lorem Ipsum is simply dummy text of the printing and typesetting industry. Lorem Ipsum has been the industry's standard...</p>
  </div>
  <div class="abs svc" style="left:799px">
    <div class="svc-icon"><span><svg width="26" height="26" viewBox="0 0 26 26"><path d="M3 11h5v12H3zM8 12l5-9c2 0 3 2 2 5h7c2 0 2 3 0 3 2 0 2 3 0 3 2 0 2 3 0 3 1 0 1 4-1 4H8" fill="none" stroke="#fff" stroke-width="1.6"/></svg></span></div>
    <h3>FOOD ADVICE</h3>
    <p>Lorem Ipsum is simply dummy text of the printing and typesetting industry. Lorem Ipsum has been the industry's standard...</p>
  </div>
</section>

<section>
  <h2 class="abs sec-title about-title">ABOUT TOVIN BRIGHTWAY</h2>
  <p class="abs about-text">Lorem Ipsum is simply dummy text of the printing and typesetting industry. Lorem Ipsum has been the industry's standard dummy text ever since the 1500s, when an unknown printer took a galley of type and scrambled it to make a type specimen book. It has survived not only five centuries, but also the leap into electronic typesetting, remaining essentially unchanged</p>
  <div class="abs divider"></div>
</section>

<section>
  <h2 class="abs block-title" style="left:174px">OUR PRODUCTS</h2>
  <div class="abs pager" style="left:695px"><svg width="7" height="10" viewBox="0 0 7 10"><path d="M6 1L2 5l4 4" fill="none" stroke="#888" stroke-width="1.5"/></svg><svg width="7" height="10" viewBox="0 0 7 10"><path d="M1 1l4 4-4 4" fill="none" stroke="#888" stroke-width="1.5"/></svg></div>

  <div class="abs card" style="left:173px">
    <div class="card-img"><div role="img" aria-label="Photo of a box of sugar-free pancake mix"></div></div>
    <h3 class="item-title">SUGAR FREE FOOD</h3>
    <p class="item-desc">Lorem Ipsum is simply dummy text of the printing and typesetting industry.</p>
    <div class="price">$ 15.00</div><div class="btn" style="left:93px;top:159px">VIEW DETAILS</div>
  </div>
  <div class="abs card" style="left:362px">
    <div class="card-img"><div role="img" aria-label="Photo of vitamin supplement bottles" style="background:linear-gradient(#f3a33a,#3a2a1c)"></div></div>
    <h3 class="item-title">SUGAR FREE FOOD</h3>
    <p class="item-desc">Lorem Ipsum is simply dummy text of the printing and typesetting industry.</p>
    <div class="price">$ 15.00</div><div class="btn" style="left:93px;top:159px">VIEW DETAILS</div>
  </div>
  <div class="abs card" style="left:551px">
    <div class="card-img"><div role="img" aria-label="Photo of a pack of sugar-free marshmallow sweets" style="width:130px;height:52px;background:linear-gradient(#f7ef8a,#d9c93a)"></div></div>
    <h3 class="item-title">SUGAR FREE FOOD</h3>
    <p class="item-desc">Lorem Ipsum is simply dummy text of the printing and typesetting industry.</p>
    <div class="price" style="top:170px">$ 15.00</div><div class="btn" style="left:93px;top:159px">VIEW DETAILS</div>
  </div>

  <h2 class="abs block-title" style="left:753px">TIPS FOR DIABETES</h2>
  <div class="abs pager" style="left:958px"><svg width="7" height="10" viewBox="0 0 7 10"><path d="M6 1L2 5l4 4" fill="none" stroke="#888" stroke-width="1.5"/></svg><svg width="7" height="10" viewBox="0 0 7 10"><path d="M1 1l4 4-4 4" fill="none" stroke="#888" stroke-width="1.5"/></svg></div>

  <div class="abs tip" style="top:912px">
    <div class="tip-img" role="img" aria-label="Photo of a glucose meter beside fresh vegetables"></div>
    <div class="tip-body"><h3 class="item-title">SUGAR FREE FOOD</h3><p class="item-desc">Lorem Ipsum is simply dummy text of the printing and typesetting.</p></div>
  </div>
  <div class="abs tip-sep"></div>
  <div class="abs tip" style="top:995px">
    <div class="tip-img" role="img" aria-label="Photo of a blood sugar test on a fingertip" style="background:linear-gradient(135deg,#e6d2c4,#3b6fa8)"></div>
    <div class="tip-body"><h3 class="item-title">SUGAR FREE FOOD</h3><p class="item-desc">Lorem Ipsum is simply dummy text of the printing and typesetting.</p></div>
  </div>
  <div class="btn" style="left:904px;top:1071px">VIEW DETAILS</div>
</section>

<footer class="abs footer">
  <div class="abs foot-links"><span>HOME</span>|<span>ABOUT US</span>|<span>SERVICES</span>|<span>PRODUCTS</span>|<span>FAQ</span>|<span>TIPS</span>|<span>TESTIMONIALS</span>|<span>FEATURES</span>|<span>CONTACT US</span></div>
  <div class="abs copy">COPYRIGHTS ©2013 TOVIN BRIGHTWAY. ALL RIGHT RESERVED</div>
  <div class="abs follow">FOLLOW US :</div>
  <div class="abs soc" style="left:889px;background:#2f62b8" aria-label="Social network 1"></div>
  <div class="abs soc" style="left:919px;background:#1d7bb9" aria-label="Social network 2"></div>
  <div class="abs soc" style="left:950px;background:#3ab0e8" aria-label="Social network 3"></div>
</footer>
</body>
</html>
```